Off Campus Housing website service for universities needs corporate brochure

We need a corporate brochure targeted at universities to get them to partner with us to offer an Off-Campus Housing website with housing listings and educational resources for their students. We provide hosted software and support, off-campus housing listings, and educational resources to embed in the university website (i.e http://rentalhub.wvx.edu); the university promotes the service to off-campus students, parents, and faculty/staff. We have a dedicated account executive to work with each university to promote the website to property managers in the schools area who pay to list their properties on the site. We currently partner with over 100 colleges and universities across the country to serve the needs of their off-campus students. Our corporate website is: www.lodgebridgeallies.com.
Updates

Target Market(s)

Universities and Colleges

Industry/Entity Type

Marketing

Font styles to use
Serif

Requirements
Must have
• Our logo
• Our website (www.lodgebridgeallies.com)
• Contact information (this is different than what we used on our previous brochure, image attached):
• Email: sales@lodgebridgeallies.com
• Student image(s) - must be diverse
• Phone: 877-461-7308
Nice to have
• University/Campus image (generic)

```html
<!DOCTYPE html>
<html lang="en">
<head>
<meta charset="utf-8">
<title>Lodge Bridge Allies — Brochure Spread</title>
<link rel="stylesheet" href="https://fonts.googleapis.com/css2?family=Libre+Caslon+Text:wght@400;700&family=Roboto+Condensed:wght@700&family=Lato:wght@400;700&display=swap">
<style>
  :root{
    --brand-blue:#0d4fa8;
    --deep-blue:#0a3f8f;
    --ink:#1b1b1b;
    --band-black:#222222;
    --paper:#ffffff;
    --paper-grey:#e9e9ea;
    --stage:#dcdcdd;
    --body-text:#f2f5fb;
  }
  *{margin:0;padding:0;box-sizing:border-box}
  html,body{width:1200px;height:1200px;overflow:hidden}
  body{
    background:linear-gradient(180deg,#e4e4e5 0%,var(--stage) 100%);
    position:relative;
    font-family:"Lato",Arial,sans-serif;
  }
  .spread{
    position:absolute;left:50px;top:174px;width:1100px;height:853px;
    box-shadow:0 12px 30px rgba(0,0,0,.28);
    display:flex;
  }
  .page{position:relative;width:550px;height:853px;overflow:hidden}
  .page svg.shapes{position:absolute;inset:0}

  /* back panel */
  .back{background:var(--brand-blue)}
  .vision{position:absolute;left:19px;top:28px;width:500px;color:var(--body-text)}
  .vision h2{font-family:"Libre Caslon Text",Georgia,serif;font-weight:400;font-size:24px;color:#fff;margin-bottom:12px}
  .vision p{font-size:10.5px;line-height:1.32;margin-bottom:12px}
  .back-contact{position:absolute;left:180px;top:680px;width:242px;text-align:center}
  .back-contact .logo-mark{font-size:14px;letter-spacing:2px}
  .back-contact .phone{font-weight:700;font-size:15px;color:var(--brand-blue);margin-top:12px}
  .back-contact .email{font-size:12px;color:var(--ink);margin-top:3px}

  .pill{
    position:absolute;height:24px;border-radius:12px;
    color:#fff;font-size:11px;letter-spacing:4px;
    display:flex;align-items:center;justify-content:center;
  }
  .pill-dark{left:37px;top:790px;width:480px;background:var(--band-black)}
  .pill-blue{left:33px;top:788px;width:478px;background:var(--brand-blue)}

  /* logo */
  .logo-mark{
    display:inline-flex;align-items:center;gap:8px;
    font-family:"Libre Caslon Text",Georgia,serif;font-weight:400;
    color:var(--brand-blue);text-transform:uppercase;white-space:nowrap;
  }
  .logo-mark .square{width:12px;height:12px;background:var(--brand-blue);display:inline-block}

  /* front cover */
  .front{background:linear-gradient(180deg,var(--paper-grey) 0%,#f7f7f7 30%,var(--paper) 60%)}
  .front .logo-mark{position:absolute;left:0;right:0;top:74px;justify-content:center;font-size:24px;letter-spacing:4px}
  .headline{position:absolute;left:33px;top:632px;width:490px;color:var(--ink)}
  .headline .lead{font-family:"Libre Caslon Text",Georgia,serif;font-size:24px;line-height:1}
  .headline .main{font-family:"Roboto Condensed",Arial Narrow,sans-serif;font-weight:700;font-size:64px;color:var(--brand-blue);line-height:1;margin-top:4px;letter-spacing:-.5px}
  .headline .sub{font-family:"Libre Caslon Text",Georgia,serif;font-size:35px;line-height:1;margin-top:2px}
</style>
</head>
<body>
<main class="spread">

  <section class="page back">
    <svg class="shapes" width="550" height="853" viewBox="0 0 550 853">
      <defs>
        <linearGradient id="campus-tone" x1="0" y1="0" x2="1" y2="1">
          <stop offset="0" stop-color="#dcdcdc"/>
          <stop offset=".5" stop-color="#f4f4f4"/>
          <stop offset="1" stop-color="#ffffff"/>
        </linearGradient>
        <radialGradient id="students-tone" cx=".5" cy=".45" r=".6">
          <stop offset="0" stop-color="#8a6a52"/>
          <stop offset=".5" stop-color="#6f8bb3"/>
          <stop offset="1" stop-color="#f3f3f3"/>
        </radialGradient>
      </defs>
      <path d="M550,244 C300,252 70,432 26,853 L550,853 Z" fill="var(--deep-blue)"/>
      <path d="M550,250 C302,258 82,438 40,853 L550,853 Z" fill="var(--band-black)"/>
      <path d="M550,268 C305,276 100,450 58,853 L550,853 Z" fill="url(#campus-tone)" role="img" aria-label="Faded photo of classical university columns"/>
      <circle cx="154" cy="456" r="124" fill="var(--band-black)"/>
      <circle cx="154" cy="456" r="118" fill="var(--brand-blue)"/>
      <circle cx="154" cy="456" r="112" fill="url(#students-tone)" role="img" aria-label="Photo of four diverse students standing with backpacks and books"/>
    </svg>

    <div class="vision">
      <h2>Vision</h2>
      <p>Lodge Bridge Allies' vision is to become the premiere provider of services to the off-campus population. We are passionate about our mission to provide best-in-class real estate listings and services to students, parents, and faculty/staff in an environment that promotes growth and development for our team members.</p>
      <p>Our corporate values - honesty, fairness, respect, and excellence allow us to develop long-term partnerships with our clients, customers, and team members.</p>
      <p>Lodge Bridge Allies provides software and services to simplify the off-campus housing search process for universities, students, and property managers. Our private-label software platform and listing program powers the off-campus housing service at many of the nation's leading universities.</p>
    </div>

    <div class="back-contact">
      <span class="logo-mark"><span class="square"></span>Lodge Bridge Allies</span>
      <p class="phone">877-461-7308</p>
      <p class="email">sales@lodgebridgeallies.com</p>
    </div>
    <div class="pill pill-dark">www.lodgebridgeallies.com.</div>
  </section>

  <section class="page front">
    <svg class="shapes" width="550" height="853" viewBox="0 0 550 853">
      <defs>
        <linearGradient id="study-tone" x1="0" y1="0" x2="0" y2="1">
          <stop offset="0" stop-color="#d9d2c6"/>
          <stop offset=".35" stop-color="#e59a5a"/>
          <stop offset=".6" stop-color="#9fb3cf"/>
          <stop offset=".85" stop-color="#f1f1f1"/>
          <stop offset="1" stop-color="#ffffff"/>
        </linearGradient>
      </defs>
      <path d="M0,262 C160,232 360,205 550,200 L550,617 L0,617 Z" fill="url(#study-tone)" role="img" aria-label="Photo of a student sitting on the floor with a laptop in a bright living room"/>
      <path d="M0,226 C160,198 360,174 550,166 L550,186 C360,192 160,216 0,246 Z" fill="var(--band-black)"/>
      <path d="M0,250 C160,222 360,196 550,190 L550,202 C360,207 160,234 0,264 Z" fill="var(--brand-blue)"/>
    </svg>

    <span class="logo-mark"><span class="square"></span>Lodge Bridge Allies</span>

    <div class="headline">
      <p class="lead">SIMPLIFYING</p>
      <h1 class="main">THE OFF-CAMPUS</h1>
      <p class="sub">HOUSING EXPERIENCE</p>
    </div>
    <div class="pill pill-blue">www.lodgebridgeallies.com.</div>
  </section>

</main>
</body>
</html>
```